Business card design for my company.
I would like the card's background colour to be black. You can also see our web site to get an idea of our brand. https://www.tmwhomecrafting.com.au/
- Name
- Email

```html
<!DOCTYPE html>
<html lang="en">
<head>
<meta charset="utf-8">
<title>TMW Home Crafting – Business Card</title>
<link rel="stylesheet" href="https://fonts.googleapis.com/css2?family=Montserrat:wght@400;500;700&display=swap">
<style>
  :root {
    --stage: #3a3a3a;
    --card: #050505;
    --white: #f4f4f4;
    --green: #12964a;
    --muted: #e6e6e6;
  }
  * { box-sizing: border-box; margin: 0; padding: 0; }
  html, body {
    width: 1200px;
    height: 875px;
    overflow: hidden;
    background: var(--stage);
    font-family: "Montserrat", sans-serif;
  }
  .canvas {
    position: relative;
    width: 1200px;
    height: 875px;
  }
  .card {
    position: absolute;
    width: 520px;
    height: 300px;
    background: var(--card);
    border-radius: 16px;
    box-shadow: 0 18px 40px rgba(0,0,0,.45);
  }
  .card--front { left: 70px; top: 110px; }
  .card--back  { left: 610px; top: 465px; }

  .wordmark {
    display: flex;
    align-items: center;
    gap: 12px;
    color: var(--white);
    font-weight: 700;
    letter-spacing: 3px;
    text-transform: uppercase;
    white-space: nowrap;
  }
  .wordmark__square {
    width: 14px;
    height: 14px;
    background: var(--green);
    flex: none;
  }
  .card--front .wordmark {
    position: absolute;
    left: 0; right: 0; top: 0; bottom: 0;
    justify-content: center;
    font-size: 28px;
  }
  .card--back .wordmark {
    position: absolute;
    left: 0; right: 0;
    top: 70px;
    justify-content: center;
    font-size: 24px;
  }

  .holder {
    position: absolute;
    left: 40px;
    top: 180px;
  }
  .holder__name {
    font-size: 22px;
    font-weight: 700;
    color: var(--white);
  }
  .holder__name .first { color: var(--green); }
  .holder__role {
    margin-top: 4px;
    font-size: 12px;
    font-weight: 500;
    color: var(--muted);
  }
  .divider {
    position: absolute;
    left: 235px;
    top: 168px;
    width: 2px;
    height: 72px;
    background: var(--green);
  }
  .contact {
    position: absolute;
    left: 258px;
    top: 170px;
    list-style: none;
  }
  .contact li {
    display: flex;
    align-items: center;
    gap: 9px;
    font-size: 12px;
    color: var(--muted);
    margin-bottom: 8px;
    white-space: nowrap;
  }
  .contact svg { width: 13px; height: 13px; flex: none; }
</style>
</head>
<body>
<main class="canvas">

  <section class="card card--front" aria-label="Card front">
    <div class="wordmark">
      <span class="wordmark__square"></span>
      <span class="wordmark__name">TMW Home Crafting</span>
    </div>
  </section>

  <section class="card card--back" aria-label="Card back">
    <div class="wordmark">
      <span class="wordmark__square"></span>
      <span class="wordmark__name">TMW Home Crafting</span>
    </div>

    <div class="holder">
      <p class="holder__name"><span class="first">John</span> Smith</p>
      <p class="holder__role">Managing Director</p>
    </div>

    <span class="divider"></span>

    <ul class="contact">
      <li>
        <svg viewBox="0 0 16 16" aria-hidden="true"><path fill="#12964a" d="M3.5 1.5l2.5 0 1 3.5-1.6 1.2a8 8 0 0 0 4.4 4.4L11 9l3.5 1v2.5c0 1-1 2-2 2C6.5 14.5 1.5 9.5 1.5 3.5c0-1 1-2 2-2z"/></svg>
        (08) 9000 4821
      </li>
      <li>
        <svg viewBox="0 0 16 16" aria-hidden="true"><rect x="1" y="3" width="14" height="10" rx="1" fill="#12964a"/><path d="M1.5 3.8L8 9l6.5-5.2" stroke="#050505" stroke-width="1.4" fill="none"/></svg>
        info@tmwhomecrafting.com.au
      </li>
      <li>
        <svg viewBox="0 0 16 16" aria-hidden="true"><circle cx="8" cy="8" r="6.5" fill="none" stroke="#12964a" stroke-width="1.5"/><ellipse cx="8" cy="8" rx="2.6" ry="6.5" fill="none" stroke="#12964a" stroke-width="1.2"/><path d="M1.5 8h13" stroke="#12964a" stroke-width="1.2"/></svg>
        www.tmwhomecrafting.com.au
      </li>
    </ul>
  </section>

</main>
</body>
</html>
```